New career and executive coaching business needs a business card design including logo

Company name: 'Bramblefield Growth Partners.' The aim of my coaching engagements is to help people improve their communication in the workplace and achieve their career goals. The process involves working with individuals to help them uncover their strengths and talents, then leverage those to improve their working lives. The Tarwick Inventory is the starting point to the process. I am after an exciting and interesting business card design (including logo)which is professional yet will still get people's attention.

Industry/Entity Type

Business

Contact Information for Business Card

Name: Malcolm Dervaney
Position: Owner
Address: 58 Quorrin Ct, Elmbridge Vic 3190
Phone: 0418923047
Website: bramblefieldgrowth.com.au
Email: malcolm@bgp.com.au

Colors
33a6d7
00a990
0355a3
3176b5

Requirements
Must have
• logo

```html
<!DOCTYPE html>
<html lang="en">
<head>
<meta charset="utf-8">
<title>Bramblefield Growth Partners – Business Card</title>
<link rel="stylesheet" href="https://fonts.googleapis.com/css2?family=Quicksand:wght@700&family=Roboto:wght@400;500&display=swap">
<style>
  :root {
    --bg: #e9edf1;
    --card: #f7f6f2;
    --sky: #1b9ad8;
    --deep: #1f6fb5;
    --icon: #1d6cb3;
    --ring: #7cc6ea;
    --shadow: rgba(20, 40, 60, 0.18);
  }
  * { box-sizing: border-box; margin: 0; padding: 0; }
  html, body {
    width: 1200px;
    height: 800px;
    overflow: hidden;
    background: var(--bg);
  }
  .canvas {
    width: 1200px;
    height: 800px;
    display: flex;
    align-items: center;
    justify-content: center;
  }
  .card {
    position: relative;
    width: 980px;
    height: 560px;
    background: var(--card);
    box-shadow: 0 14px 40px var(--shadow);
    overflow: hidden;
  }
  .band {
    position: absolute;
    left: 0;
    right: 0;
    height: 36px;
    display: flex;
  }
  .band--top { top: 0; }
  .band--bottom { bottom: 0; }
  .band__light { background: var(--sky); }
  .band__dark { background: var(--deep); flex: 1; }
  .band--top .band__light { width: 46%; }
  .band--bottom .band__light { width: 60%; }

  .identity {
    position: absolute;
    top: 84px;
    right: 80px;
    text-align: right;
  }
  .identity__name {
    font-family: 'Quicksand', sans-serif;
    font-weight: 700;
    font-size: 40px;
    color: var(--deep);
    line-height: 1;
  }
  .identity__role {
    font-family: 'Roboto', sans-serif;
    font-weight: 500;
    font-size: 17px;
    letter-spacing: 3px;
    color: var(--sky);
    margin-top: 6px;
  }

  .brand {
    position: absolute;
    top: 190px;
    right: 80px;
    display: flex;
    align-items: center;
    gap: 18px;
  }
  .brand__dot {
    width: 54px;
    height: 54px;
    border-radius: 50%;
    background: var(--ring);
    flex: none;
  }
  .brand__name {
    font-family: 'Quicksand', sans-serif;
    font-weight: 700;
    font-size: 26px;
    line-height: 1.15;
    color: var(--ring);
    width: 220px;
  }

  .contacts {
    position: absolute;
    left: 90px;
    top: 320px;
    list-style: none;
  }
  .contacts__item {
    display: flex;
    align-items: center;
    gap: 30px;
    height: 48px;
    margin-bottom: 22px;
  }
  .contacts__icon {
    width: 48px;
    height: 48px;
    background: var(--icon);
    display: flex;
    align-items: center;
    justify-content: center;
    flex: none;
  }
  .contacts__text {
    font-family: 'Roboto', sans-serif;
    font-size: 21px;
    color: var(--sky);
  }
</style>
</head>
<body>
<main class="canvas">
  <section class="card" aria-label="Business card for Bramblefield Growth Partners">
    <div class="band band--top"><div class="band__light"></div><div class="band__dark"></div></div>

    <header class="identity">
      <h1 class="identity__name">Malcolm Dervaney</h1>
      <p class="identity__role">OWNER</p>
    </header>

    <div class="brand">
      <span class="brand__dot"></span>
      <span class="brand__name">Bramblefield Growth Partners</span>
    </div>

    <ul class="contacts">
      <li class="contacts__item">
        <span class="contacts__icon">
          <svg width="26" height="26" viewBox="0 0 24 24" aria-hidden="true"><path fill="#fff" d="M6.6 10.8a15.1 15.1 0 0 0 6.6 6.6l2.2-2.2a1 1 0 0 1 1-.25 11.4 11.4 0 0 0 3.6.57 1 1 0 0 1 1 1V20a1 1 0 0 1-1 1A17 17 0 0 1 3 4a1 1 0 0 1 1-1h3.5a1 1 0 0 1 1 1c0 1.25.2 2.45.57 3.57a1 1 0 0 1-.25 1z"/></svg>
        </span>
        <span class="contacts__text">0418923047</span>
      </li>
      <li class="contacts__item">
        <span class="contacts__icon">
          <svg width="28" height="22" viewBox="0 0 28 22" aria-hidden="true"><rect x="1.5" y="1.5" width="25" height="19" fill="none" stroke="#fff" stroke-width="2"/><path d="M1.5 1.5 14 12 26.5 1.5M1.5 20.5l9-8.5M26.5 20.5l-9-8.5" fill="none" stroke="#fff" stroke-width="2"/></svg>
        </span>
        <span class="contacts__text">malcolm@bgp.com.au</span>
      </li>
      <li class="contacts__item">
        <span class="contacts__icon">
          <svg width="22" height="28" viewBox="0 0 22 28" aria-hidden="true"><path fill="#fff" d="M11 1a9 9 0 0 0-9 9c0 6.8 9 17 9 17s9-10.2 9-17a9 9 0 0 0-9-9zm0 12.5A3.5 3.5 0 1 1 11 6.5a3.5 3.5 0 0 1 0 7z"/></svg>
        </span>
        <span class="contacts__text">58 Quorrin Ct, Elmbridge Vic 3190</span>
      </li>
    </ul>

    <div class="band band--bottom"><div class="band__light"></div><div class="band__dark"></div></div>
  </section>
</main>
</body>
</html>
```